Harvest Gateway Fellowship Ministries needs a fresh new web design

We are an up and coming multicultural church that aims to bring people into a life changing encounter with God. We need a fresh and inviting website in order to increase our internet presence and make us easier to connect with.
Here are some of the basic requirements for the site:
• Clearly displayed address, service times, and contact info
• A staff profile page
• An area for a calendar with upcoming events and their details
• Social media buttons
• Group pages for the different ministries (youth, children’s church, men, etc…)
• An area for donations and eCommerce
• A resources page for assorted media (podcasts, sermons, videos, etc.…)
• An area for prayer requests.

```html
<!DOCTYPE html>
<html lang="en">
<head>
<meta charset="utf-8">
<title>Resource Center – Harvest Gateway Fellowship Ministries</title>
<link rel="stylesheet" href="https://fonts.googleapis.com/css2?family=Lato:wght@300;400;700&family=Cormorant+Garamond:wght@500&display=swap">
<style>
:root{
  --navy:#1d1497;
  --navy-deep:#1a0f8c;
  --gold:#e2b810;
  --gold-text:#d9ad0c;
  --page:#f0f0f0;
  --white:#ffffff;
  --ink:#333333;
  --muted:#777777;
  --faint:#aaaaaa;
  --player:#2f2f2f;
  --player-track:#555555;
  --line:#e4e4e4;
}
*{box-sizing:border-box;margin:0;padding:0}
html,body{width:821px;height:1200px;overflow:hidden}
body{font-family:'Lato',sans-serif;color:var(--ink);background:var(--page);position:relative}
.abs{position:absolute}

/* top bar */
.topbar{left:0;top:0;width:821px;height:27px;background:var(--navy);color:var(--white);font-size:9.5px}
.topbar .tagline{left:68px;top:9px}
.topbar .schedule-label{left:504px;top:9px;font-size:9px}
.topbar .schedule-times{left:631px;top:3px;padding-left:7px;border-left:1px solid var(--white);font-size:8px;line-height:10px}

/* header */
.header{left:0;top:27px;width:821px;height:79px;background:var(--white)}
.brand{left:70px;top:17px;display:flex;align-items:center;gap:6px}
.brand .dot{width:34px;height:34px;border-radius:50%;background:var(--gold)}
.brand .name{font-size:12px;font-weight:700;color:var(--navy);line-height:14px;width:140px}
.info{top:16px;text-align:right;font-size:9px;color:#555;line-height:11px}
.info h4{font-size:11px;font-weight:700;color:#444;margin-bottom:3px}
.info a{color:var(--gold-text);font-size:8px;text-decoration:none;display:block;margin-top:1px}
.info.donate{left:270px;width:122px}
.info.prayer{left:416px;width:168px;border-left:1px solid #ddd}
.info.address{left:600px;width:107px;border-left:1px solid #ddd}
.social-top{left:734px;top:19px}
.social-top span{display:block;width:18px;height:18px;border-radius:50%;background:#9a9a9a;margin-bottom:3px}

/* nav */
.nav{left:0;top:106px;width:821px;height:27px;background:var(--gold);display:flex;justify-content:center;font-size:9.5px;color:#4a3b00}
.nav ul{display:flex;list-style:none;margin-left:-10px}
.nav li{padding:0 18px;line-height:27px;border-left:1px solid rgba(0,0,0,.12)}
.nav li:first-child{border-left:0}

/* banner */
.banner{left:0;top:133px;width:821px;height:69px;background:linear-gradient(90deg,#2a1b0c 0%,#5a3a14 35%,#3a2810 60%,#6b4916 85%,#2e1f0b 100%)}
.crumb{left:68px;top:153px;color:var(--white);font-size:8.5px}
.page-title{left:68px;top:163px;color:var(--white);font-size:18px;font-weight:700}

/* filter */
.filter{left:75px;top:240px;display:flex;align-items:baseline;font-size:13px;color:#555;font-weight:300}
.filter .label{font-size:9px;color:var(--muted);margin-right:8px;font-weight:400}
.filter span.sep{color:#ccc;margin:0 12px}
.filter .active{color:var(--gold-text)}

/* cards */
.card{background:var(--white);box-shadow:0 1px 2px rgba(0,0,0,.12);width:246px}
.player{height:20px;background:var(--player);display:flex;align-items:center;padding:0 6px;gap:6px}
.player .play{width:0;height:0;border-left:6px solid #ddd;border-top:4px solid transparent;border-bottom:4px solid transparent;margin-right:4px}
.player .track{flex:1;height:4px;background:var(--player-track);position:relative;border-left:1px solid #1e1e1e;margin-left:4px}
.player .track i{position:absolute;left:4px;top:0;height:4px;width:70px;background:#f0e000}
.player .vol{width:8px;height:7px;background:#ddd;clip-path:polygon(0 30%,40% 30%,100% 0,100% 100%,40% 70%,0 70%);margin-left:6px}
.player .vbar{width:22px;height:4px;background:#f0e000;margin-right:6px}
.thumb{height:160px;background:linear-gradient(180deg,#3d2f6e 0%,#6e5a9c 40%,#b88aa8 70%,#e4b39a 100%);display:flex;flex-direction:column;justify-content:center;align-items:center;color:var(--white);font-family:'Cormorant Garamond',serif;font-size:27px;line-height:32px;font-weight:500}
.card .body{text-align:center;padding:0 16px}
.card h3{font-size:16px;font-weight:400;color:#333}
.card .kind{font-size:10px;color:var(--faint)}
.card .artist{font-size:9px;color:#333}
.card p{font-size:8.7px;line-height:13.5px;color:#555;margin-top:11px}
.card .foot{border-top:1px solid var(--line);height:26px;display:flex;align-items:center;justify-content:space-between;padding:0 13px;font-size:8px;color:#888}
.card .share{display:flex;align-items:center;gap:2px;color:#ccc}
.card .share b{width:14px;height:14px;border-radius:50%;background:#ddd;display:inline-block}

/* archive */
.archive{left:609px;top:240px;width:137px;font-size:9.5px}
.archive h2{font-size:16px;font-weight:400;color:var(--gold-text);border-bottom:1px solid var(--gold-text);padding-bottom:2px}
.year{display:flex;align-items:center;justify-content:space-between;color:var(--gold-text);font-size:10px}
.year .folder{display:inline-block;width:9px;height:7px;background:var(--gold-text);margin-right:5px}
.year .toggle{width:13px;height:13px;border-radius:50%;background:var(--gold-text);color:var(--white);font-size:11px;line-height:13px;text-align:center;font-weight:700}
.months{list-style:none;padding-left:6px;margin-top:9px}
.months li{height:24px;line-height:24px;border-bottom:1px solid #e0e0e0;color:#555}
.months li.current{color:var(--gold-text)}
.months li small{color:#888;font-size:9.5px}

/* footer */
.footer{left:0;top:993px;width:821px;height:207px;background:var(--navy-deep);color:#b8b4e6;font-size:8.5px}
.footer h5{font-size:12px;font-weight:400;color:#cfcdf5;margin-bottom:8px}
.fcol{top:30px;line-height:12px}
.fcol.contact{left:68px}
.fcol.communities{left:220px}
.fcol.newsletter{left:410px}
.fcol.connect{left:600px}
.fcol .row{display:flex;align-items:center;gap:8px;margin-top:8px}
.links{display:flex;gap:14px;list-style:none}
.links ul{list-style:none}
.links li{line-height:16.5px}
.links li::before{content:"• "}
.email-field{width:156px;height:22px;background:var(--white);border-radius:2px;color:#bbb;padding:5px 8px;margin-top:8px;font-size:8.5px}
.subscribe{display:inline-block;background:var(--gold);color:#3a2c00;padding:5px 13px;border-radius:2px;margin-top:8px}
.fsocial{display:flex;gap:6px;margin-top:10px}
.fsocial span{width:22px;height:22px;border-radius:50%;background:#8e86cf}
.footer .rule{left:0;top:152px;width:821px;height:1px;background:rgba(255,255,255,.12)}
.copyright{left:0;top:166px;width:821px;text-align:center;font-size:7.5px;color:#9892d8}
</style>
</head>
<body>

<div class="abs topbar">
  <div class="abs tagline">A house of prayer for all nations, where the love, the presence and the power of God are real.</div>
  <div class="abs schedule-label">SUNDAY SERVICE SCHEDULE</div>
  <div class="abs schedule-times">09:00 A.M. | Sunday School<br>10:30 A.M. | Convergent Service</div>
</div>

<header class="abs header">
  <div class="abs brand"><span class="dot"></span><span class="name">HARVEST GATEWAY FELLOWSHIP MINISTRIES</span></div>
  <div class="abs info donate"><h4>Donate</h4>Lorem Ipsum is simply dummy text of the printing<a>Donate Now »</a></div>
  <div class="abs info prayer"><h4>Request Prayer</h4>Lorem Ipsum is simply dummy text of the printing and typesetting industry.<a>Request Now »</a></div>
  <div class="abs info address"><h4>Address</h4>Harvest Gateway City, Location<a>Contact »</a></div>
  <div class="abs social-top"><span></span><span></span></div>
</header>

<nav class="abs nav"><ul>
  <li>Home</li><li>About</li><li>Staff Profile</li><li>News and Events</li><li>Worship &amp; Services</li><li>Groups</li><li>Shop</li><li>Resources</li><li>Contact</li>
</ul></nav>

<div class="abs banner" role="img" aria-label="Warm dark photo of a wheat field at dusk"></div>
<div class="abs crumb">Home &gt; Resource Center</div>
<h1 class="abs page-title">Resource Center</h1>

<div class="abs filter">
  <span class="label">Filter by</span><span class="active">All</span><span class="sep">|</span>Sunday Sermon<span class="sep">|</span>Radio Shows<span class="sep">|</span>Bible Study<span class="sep">|</span>Videos
</div>

<!-- left column -->
<article class="abs card" style="left:75px;top:271px;height:173px">
  <div class="player"><span class="play"></span><span class="track"><i></i></span><span class="vol"></span><span class="vbar"></span></div>
  <div class="body" style="padding-top:31px;height:127px"><h3>Sunday Sermon</h3><div class="kind">Audio</div><p>Lorem Ipsum is simply dummy text of the printing and typesetting industry lorem Ipsum has been the industry's standard dummy text.</p></div>
  <div class="foot"><span>31-Jul-14</span><span class="share">Share <b></b><b></b></span></div>
</article>

<article class="abs card" style="left:75px;top:452px;height:173px">
  <div class="player"><span class="play"></span><span class="track"><i></i></span><span class="vol"></span><span class="vbar"></span></div>
  <div class="body" style="padding-top:31px;height:127px"><h3>Radio Show</h3><div class="kind">Audio</div><p>Lorem Ipsum is simply dummy text of the printing and typesetting industry lorem Ipsum has been the industry's standard dummy text.</p></div>
  <div class="foot"><span>24-Jul-14</span><span class="share">Share <b></b><b></b></span></div>
</article>

<article class="abs card" style="left:75px;top:632px;height:320px">
  <div class="thumb" role="img" aria-label="Video still of a purple sunset sky with the song title"><span>I Surrender All</span><span>Jordan Ellery</span></div>
  <div class="player"><span class="play"></span><span class="track"><i></i></span><span class="vol"></span><span class="vbar"></span></div>
  <div class="body" style="padding-top:17px;height:114px"><h3>I Surrender All</h3><div class="artist">Jordan Ellery</div><p style="margin-top:8px">A worship song we play for worship at out church. I have put this is video format for that purpose. All rights reserved to the artist.</p></div>
  <div class="foot"><span>06-Jul-14</span><span class="share">Share <b></b><b></b></span></div>
</article>

<!-- right column -->
<article class="abs card" style="left:328px;top:271px;height:320px">
  <div class="thumb" role="img" aria-label="Video still of a purple sunset sky with the song title"><span>I Surrender All</span><span>Jordan Ellery</span></div>
  <div class="player"><span class="play"></span><span class="track"><i></i></span><span class="vol"></span><span class="vbar"></span></div>
  <div class="body" style="padding-top:17px;height:114px"><h3>I Surrender All</h3><div class="artist">Jordan Ellery</div><p style="margin-top:8px">A worship song we play for worship at out church. I have put this is video format for that purpose. All rights reserved to the artist.</p></div>
  <div class="foot"><span>30-Jul-14</span><span class="share">Share <b></b><b></b></span></div>
</article>

<article class="abs card" style="left:328px;top:598px;height:173px">
  <div class="player"><span class="play"></span><span class="track"><i></i></span><span class="vol"></span><span class="vbar"></span></div>
  <div class="body" style="padding-top:31px;height:127px"><h3>Bible Study</h3><div class="kind">Audio</div><p>Lorem Ipsum is simply dummy text of the printing and typesetting industry lorem Ipsum has been the industry's standard dummy text.</p></div>
  <div class="foot"><span>24-Jul-14</span><span class="share">Share <b></b><b></b></span></div>
</article>

<article class="abs card" style="left:328px;top:779px;height:173px">
  <div class="player"><span class="play"></span><span class="track"><i></i></span><span class="vol"></span><span class="vbar"></span></div>
  <div class="body" style="padding-top:31px;height:127px"><h3>Radio Show</h3><div class="kind">Audio</div><p>Lorem Ipsum is simply dummy text of the printing and typesetting industry lorem Ipsum has been the industry's standard dummy text.</p></div>
  <div class="foot"><span>02-Jul-14</span><span class="share">Share <b></b><b></b></span></div>
</article>

<!-- archive -->
<aside class="abs archive">
  <h2>ARCHIVE</h2>
  <div class="year" style="margin-top:7px"><span><span class="folder"></span>2014</span><span class="toggle">−</span></div>
  <ul class="months">
    <li class="current">Jul 2014 <small>(24)</small></li>
    <li>Jun 2014 <small>(18)</small></li>
    <li>May 2014 <small>(19)</small></li>
    <li>Apr 2014 <small>(34)</small></li>
    <li>Mar 2014 <small>(54)</small></li>
    <li>Feb 2014 <small>(29)</small></li>
    <li style="border-bottom:0">Jan 2014 <small>(19)</small></li>
  </ul>
  <div class="year" style="margin-top:20px"><span><span class="folder"></span>2013</span><span class="toggle">+</span></div>
  <div class="year" style="margin-top:16px"><span><span class="folder"></span>2012</span><span class="toggle">+</span></div>
</aside>

<footer class="abs footer">
  <div class="abs fcol contact">
    <h5>CONTACT US</h5>
    Harvest Gateway<br>Location, city<br>State Name, Country
    <div class="row"><svg width="10" height="10" viewBox="0 0 10 10"><path d="M2 0.5 L4 2.5 L3 4 Q4.5 6 6 7 L7.5 6 L9.5 8 L8 9.5 Q3 9 0.5 2 Z" fill="#b8b4e6"/></svg><span style="font-size:9.5px">+1 888-555-0142</span></div>
    <div class="row" style="margin-top:3px"><svg width="10" height="8" viewBox="0 0 10 8"><rect x="0.5" y="0.5" width="9" height="7" fill="none" stroke="#b8b4e6"/><path d="M0.5 0.5 L5 4.5 L9.5 0.5" fill="none" stroke="#b8b4e6"/></svg><span style="font-size:9.5px">hello@harvestgateway.org</span></div>
  </div>
  <div class="abs fcol communities">
    <h5>COMMUNITIES WE SERVE</h5>
    <div class="links">
      <ul><li>Lorem Ipsum</li><li>Dummy Links</li><li>More dummy</li><li>Sample Text</li><li>More samples</li></ul>
      <ul><li>type text dummy</li><li>Lorem Ipsum</li></ul>
    </div>
  </div>
  <div class="abs fcol newsletter">
    <h5>NEWSLETTER</h5>
    Enter your email below to get notified
    <div class="email-field">Your Email</div>
    <span class="subscribe">Subscribe</span>
  </div>
  <div class="abs fcol connect">
    <h5>CONNECT WITH US</h5>
    Stay connected for the latest updates at<br>Harvest Gateway Fellowship
    <div class="fsocial"><span></span><span></span></div>
  </div>
  <div class="abs rule"></div>
  <div class="abs copyright">Copyright © 2014. All rights reserved. Harvest Gateway.</div>
</footer>

</body>
</html>
```